Velantry Guest Event Collateral

Create a double-sided, oversized piece of collateral for a series of guest networking events that we'll be hosting in 2019

We are looking for this piece of collateral to be the size of an oversized post card (1/2 of an 8/5 x 11 piece of paper). The front should include the following: Velantry's Mission Statement: Continually foster a culture of community and education for focused business professionals. How do we do it? Using four distinct principles, Velantry offers business professionals the opportunity to be successful right now ,as well as next year. Through in-person meetings, virtual meetings, networking events, and educational opportunities Velantry offers members a chance to hit their goals not only this year, but every year! Collaboration: Work with like-minded, driven Velantry members to collaborate and overcome the objections, hurdles and challenges that all business professionals face, either in person at twice monthly meetings, or virtually, from the comfort of your home or office. Accountability: Stay on track, and complete the goals you have set for yourself! Weekly in person or virtual meetings afford all members the opportunity to review their plan twice a month with fellow Velantry members, and trained Velantry coaches. Referrals: In the midst of crafting an executable, measurable and attainable plan let Velantry build your business through a steady stream of referrals via six yearly networking events, specifically designed to ensure you walk away with new referral partners. Strategy: Let Velantry assist you in crafting a strategy within our proven business planning template; realistic, understandable, measurable, beyond normal, attainable and time bound. The back should include the following: Become a Velantry member for $150/month and join us for 6 Networking Events in 2019 plus much more! We aren’t just about collaboration, accountability and strategy! Creating opportunities for referrals is also a cornerstone of Velantry! To make certain we are delivering on this principle, Velantry will host 6 events throughout 2019, complete with specific activities at each event to ensure you meet everyone in the room, making immediate connects to build your referral network. Join now and put yourself in position for success in 2019! Name: Phone: Email: Company Name: Industry: Position: Credit Card Number: Exp. Date: Testimonials: Overall I think people are lazy. I know I am! The benefits I have found and have come to truly appreciate thru Velantry are a sense of professionalism, accountability and shared enthusiasm. These things break that cycle of laziness for me and, I am sure, many others. When I walk into a meeting I know that positive and helpful feedback is the name of the game. Feedback from others and in many other industries from my own has become a key and cornerstone to my business and personal success. I would urge anyone no matter what your occupation to attend a couple of meetings and see how this group of like minded professionals can help you to achieve more. More time, More success, More health, More security, More money, More happiness..............What could you use more of? Desmond K. Ferrow Sr. Automotive Consultant Brookmere Motors & Rentals Thank you!

Target Market(s)

Small business owners, entrpreneurs, networkers, sales people

Industry/Entity Type

Business Consultant

Font styles to use
Sans Serif

Colors
f36f22
f68d4e
f8ba93
f78f20
faa54b

Requirements
Must have
• - Imagery
• - Our company logo
• - Clear CTA to check out our website (www.velantry-example.com)
• - Option to "Join the Velantry Community Today!" and include a spot for someone to fill in their name, email address, company name, and phone number
• - Reference that we host 6+ networking events in Denver throughout the year that are free to attend and are unlike any other networking event they've attended before
• - Mention that we have in-person meetings 2x per month, virtual meeting options, networking events, and educational events
• - Highlight the following acronym which references our core company components:
• Collaboration:
• Work with like-minded, driven Velantry members to collaborate and overcome the objections, hurdles and challenges that all business professionals face, in either in person twice monthly meetings, or virtually, from the comfort of your home of office.
• Accountability:
• Stay on track, and complete the goals you have set for yourself! Weekly in person or virtual meetings afford all members the opportunity to review their plan twice a month with your fellow Velantry members and trained Velantry coaches, to make certain you success is continuous throughout the year.
• Referrals:
• In the midst of crafting an executable, measurable and attainable plan let Velantry build your business through a steady stream of referral opportunities via twelve yearly networking events, specifically designed to ensure you walk away with new referral partners.
• Strategy:
• Let Velantry assist you in crafting a strategy within our proven business planning template; realistic, understandable, measurable, beyond normal, attainable and time bound.

```html
<!DOCTYPE html>
<html lang="en">
<head>
<meta charset="utf-8">
<title>Velantry Guest Networking Events 2019</title>
<link href="https://fonts.googleapis.com/css2?family=Roboto:wght@400;500;700&family=Roboto+Condensed:wght@700&display=swap" rel="stylesheet">
<style>
  :root{
    --orange:#f36f22;
    --orange-soft:#f68d4e;
    --orange-pale:#f8ba93;
    --amber:#f78f20;
    --gray:#6d6d6f;
    --ink:#4a4a4a;
    --field:#efefef;
    --paper:#ffffff;
    --backdrop:#e6e6e6;
  }
  html,body{margin:0;padding:0;width:796px;height:1200px;overflow:hidden;background:var(--backdrop);font-family:"Roboto",sans-serif;color:var(--ink);}
  .sheet{position:absolute;left:178px;width:440px;height:570px;background:var(--paper);overflow:hidden;box-shadow:0 2px 8px rgba(0,0,0,.18);}
  .sheet--front{top:20px;}
  .sheet--back{top:610px;}
  .sheet__art{position:absolute;inset:0;width:440px;height:570px;}
  .photo{position:absolute;left:0;top:0;width:440px;}
  .photo--desk{height:260px;background:linear-gradient(135deg,#f2b183,#f3dccb 55%,#e6c3a5);clip-path:path('M0,0 H440 V176 C420,200 380,215 300,224 C190,236 60,246 0,256 Z');}
  .photo--laptop{height:340px;background:linear-gradient(135deg,#d9cfc8,#f3e3d6 45%,#e9b996);clip-path:path('M0,0 H440 V276 C410,290 350,296 250,300 C150,304 60,305 20,314 C8,317 2,322 0,328 Z');}
  .logo-tab{position:absolute;left:0;top:0;}
  .logo{position:absolute;left:22px;top:36px;display:flex;align-items:center;gap:6px;font-size:17px;letter-spacing:.5px;color:var(--gray);}
  .logo__mark{width:14px;height:14px;background:var(--orange);}
  .headline{position:absolute;left:22px;top:268px;font-family:"Roboto Condensed",sans-serif;font-weight:700;line-height:1;margin:0;}
  .headline__top{display:block;font-size:18px;color:var(--orange);}
  .headline__main{display:block;font-size:29px;color:var(--orange);margin-top:2px;}
  .headline__year{color:var(--gray);}
  .intro{position:absolute;left:22px;top:330px;width:210px;font-size:8.3px;line-height:1.4;}
  .intro p{margin:0 0 7px;}
  .perks{position:absolute;left:250px;top:238px;width:180px;display:grid;grid-template-columns:1fr 1fr;gap:3px 8px;margin:0;padding:0;list-style:none;font-size:6.8px;line-height:1.25;}
  .perks li{position:relative;padding-left:8px;}
  .perks li::before{content:"★";position:absolute;left:0;color:var(--orange);font-size:6px;}
  .join{position:absolute;left:250px;top:288px;margin:0;font-family:"Roboto Condensed",sans-serif;font-weight:700;font-size:15.5px;line-height:1.1;}
  .join__accent{color:var(--orange);display:block;}
  .join__rest{color:var(--gray);display:block;}
  .signup{position:absolute;left:250px;top:330px;width:168px;height:118px;background:var(--field);padding:10px 8px;box-sizing:border-box;}
  .signup__field{display:flex;align-items:flex-end;gap:4px;font-size:5.8px;font-weight:700;color:var(--gray);height:25px;}
  .signup__line{flex:1;border-bottom:1px dotted #9a9a9a;margin-bottom:1px;}
  .cta{position:absolute;right:20px;bottom:14px;margin:0;text-align:right;color:#fff;}
  .cta__lead{display:block;font-size:10px;}
  .cta__url{display:block;font-size:11px;font-weight:700;letter-spacing:1.3px;}
  .components-title{position:absolute;left:22px;top:340px;margin:0;font-size:10px;font-weight:700;letter-spacing:.6px;color:var(--gray);}
  .component{position:absolute;box-sizing:border-box;padding-left:28px;font-size:7px;line-height:1.32;}
  .component__name{margin:0 0 3px;font-family:"Roboto Condensed",sans-serif;font-weight:700;font-size:11px;color:var(--orange);}
  .component__text{margin:0;}
  .component__icon{position:absolute;left:0;top:4px;width:20px;height:20px;}
  .component--collab{left:22px;top:360px;width:196px;}
  .component--account{left:22px;top:450px;width:196px;}
  .component--referral{left:230px;top:336px;width:196px;}
  .component--strategy{left:230px;top:420px;width:196px;}
</style>
</head>
<body>

<section class="sheet sheet--front" aria-label="Front side">
  <svg class="sheet__art" viewBox="0 0 440 570" aria-hidden="true">
    <path d="M0,256 C60,246 190,236 300,224 C380,215 420,200 440,176 V214 C410,232 360,240 300,246 C190,256 60,262 0,268 Z" fill="var(--orange-pale)" opacity=".45"/>
    <path d="M0,256 C60,246 190,236 300,224 C380,215 420,200 440,176" fill="none" stroke="var(--orange)" stroke-width="3"/>
    <path d="M440,532 V570 H0 V548 H235 C262,548 270,522 300,518 H440 Z" fill="var(--gray)"/>
    <path d="M0,544 H232 C258,544 266,516 298,512 H440" fill="none" stroke="var(--orange)" stroke-width="2.5"/>
  </svg>
  <div class="photo photo--desk" role="img" aria-label="Photo of colleagues' hands reviewing printed charts and reports on a desk"></div>
  <svg class="logo-tab" width="440" height="80" aria-hidden="true"><polygon points="0,24 178,24 158,70 0,70" fill="#fff"/></svg>
  <div class="logo"><span class="logo__mark"></span>VELANTRY</div>

  <h1 class="headline">
    <span class="headline__top">GUEST NETWORKING</span>
    <span class="headline__main">EVENTS <span class="headline__year">2019</span></span>
  </h1>
  <div class="intro">
    <p>6+ networking events in Denver throughout the year that are free to attend and are unlike any other networking event they've attended before.</p>
    <p>We founded Velantry with one objective: Help sales professionals, business owners, and entrepreneurs take a step away from the myriad daily distractions so they can create a simple, actionable business strategy.</p>
    <p>Confused by all the competing theories, terminologies, and processes? We distill these down into an easily digestible approach that allows for broad application regardless of your position, tenure, or industry.</p>
  </div>

  <ul class="perks">
    <li>In-person meetings 2x per month</li>
    <li>Networking events</li>
    <li>Virtual meeting options</li>
    <li>Educational events</li>
  </ul>
  <h2 class="join"><span class="join__accent">JOIN THE VELANTRY</span><span class="join__rest">COMMUNITY TODAY!</span></h2>
  <div class="signup">
    <div class="signup__field">NAME:<span class="signup__line"></span></div>
    <div class="signup__field">EMAIL ADDRESS:<span class="signup__line"></span></div>
    <div class="signup__field">COMPANY NAME:<span class="signup__line"></span></div>
    <div class="signup__field">PHONE NUMBER:<span class="signup__line"></span></div>
  </div>

  <p class="cta"><span class="cta__lead">For more information visit at</span><span class="cta__url">www.velantry-example.com</span></p>
</section>

<section class="sheet sheet--back" aria-label="Back side">
  <div class="photo photo--laptop" role="img" aria-label="Photo of a professional working at a laptop keyboard"></div>
  <svg class="sheet__art" viewBox="0 0 440 570" aria-hidden="true">
    <path d="M0,328 C2,322 8,317 20,314 C60,305 150,304 250,300 C350,296 410,290 440,276" fill="none" stroke="var(--orange)" stroke-width="3"/>
    <path d="M440,500 V570 H0 V548 H235 C262,548 270,516 300,512 H440 Z" fill="var(--gray)"/>
    <path d="M0,544 H232 C258,544 266,508 298,504 H440" fill="none" stroke="var(--orange)" stroke-width="2.5"/>
  </svg>

  <h2 class="components-title">OUR CORE COMPANY COMPONENTS</h2>

  <div class="component component--collab">
    <svg class="component__icon" viewBox="0 0 20 20" aria-hidden="true"><circle cx="7" cy="6" r="3.5" fill="var(--ink)"/><path d="M1,18 C1,12 13,12 13,18 Z" fill="var(--ink)"/><path d="M14,8 l4,4 M18,8 l-4,4" stroke="var(--ink)" stroke-width="1.6"/></svg>
    <h3 class="component__name">COLLABORATION:</h3>
    <p class="component__text">Work with like-minded, driven Velantry members to collaborate and overcome the objections, hurdles and challenges that all business professionals face, in either in person twice monthly meetings, or virtually, from the comfort of your home of office.</p>
  </div>
  <div class="component component--account">
    <svg class="component__icon" viewBox="0 0 20 20" aria-hidden="true"><path d="M1,4 l1.5,1.5 3,-3 M1,10 l1.5,1.5 3,-3 M1,16 l1.5,1.5 3,-3" fill="none" stroke="var(--ink)" stroke-width="1.4"/><path d="M8,4 H19 M8,10 H19 M8,16 H19" stroke="var(--ink)" stroke-width="2"/></svg>
    <h3 class="component__name">ACCOUNTABILITY:</h3>
    <p class="component__text">Stay on track, and complete the goals you have set for yourself! Weekly in person or virtual meetings afford all members the opportunity to review their plan twice a month with your fellow Velantry members and trained Velantry coaches, to make certain you success is continuous throughout the year.</p>
  </div>
  <div class="component component--referral">
    <svg class="component__icon" viewBox="0 0 20 20" aria-hidden="true"><rect x="1" y="14" width="3" height="5" fill="var(--ink)"/><rect x="6" y="11" width="3" height="8" fill="var(--ink)"/><rect x="11" y="7" width="3" height="12" fill="var(--ink)"/><rect x="16" y="2" width="3" height="17" fill="var(--ink)"/></svg>
    <h3 class="component__name">REFERRALS:</h3>
    <p class="component__text">In the midst of crafting an executable, measurable and attainable plan let Velantry build your business through a steady stream of referral opportunities via twelve yearly networking events, specifically designed to ensure you walk away with new referral partners.</p>
  </div>
  <div class="component component--strategy">
    <svg class="component__icon" viewBox="0 0 20 20" aria-hidden="true"><path d="M10,3 L20,8 L10,13 L0,8 Z" fill="var(--ink)"/><path d="M4,10 V15 C6,18 14,18 16,15 V10 L10,13 Z" fill="var(--ink)"/><path d="M18,9 V15" stroke="var(--ink)" stroke-width="1.2"/></svg>
    <h3 class="component__name">STRATEGY:</h3>
    <p class="component__text">Let Velantry assist you in crafting a strategy within our proven business planning template; realistic, understandable, measurable, beyond normal, attainable and time bound.</p>
  </div>

  <p class="cta"><span class="cta__lead">For more information visit at</span><span class="cta__url">www.velantry-example.com</span></p>
</section>

</body>
</html>
```